Business Card Design Project

After recently finishing a design project for the company logo using markbazaar, it's now time for a business card. Attached to this is the logo.

The requirements for the business card are pretty straightforward:

- A clean, uncomplicated look
- Consistent usage of fonts
- Designs for both single sided and double sided cards
- A modern layout with preferably space to refer to social media accounts and/or downloadable vcards through a qr code
- consistent application of the company colour scheme: red/white. Hex codes for exact colour can be provided

Thanks!

```html
<!DOCTYPE html>
<html lang="en">
<head>
<meta charset="utf-8">
<title>Tall Oak Staffing – Business Card</title>
<link href="https://fonts.googleapis.com/css2?family=Source+Sans+3:wght@400;600;700&display=swap" rel="stylesheet">
<style>
  :root {
    --brand-red: #e8212a;
    --ink-dark: #333333;
    --ink-mid: #3d3d3d;
    --card-white: #ffffff;
    --backdrop: #e9e6e2;
    --divider: #8a8a8a;
  }
  * { margin: 0; padding: 0; box-sizing: border-box; }
  html, body { width: 960px; height: 1200px; overflow: hidden; }
  body {
    position: relative;
    background: var(--backdrop);
    font-family: "Source Sans 3", "Myriad Pro", Arial, sans-serif;
    color: var(--ink-dark);
  }
  .card {
    position: absolute;
    background: var(--card-white);
    border-radius: 28px;
    overflow: hidden;
    box-shadow: 0 6px 14px rgba(0,0,0,0.18);
  }
  .card--front { left: 60px; top: 78px; width: 840px; height: 479px; }
  .card--back  { left: 55px; top: 637px; width: 840px; height: 480px; }

  .brand-mark {
    display: flex;
    align-items: center;
    gap: 16px;
    font-weight: 600;
    color: var(--ink-dark);
    white-space: nowrap;
  }
  .brand-mark__square { background: var(--brand-red); flex: none; }

  .card--front .brand-mark {
    position: absolute; left: 70px; top: 178px; font-size: 34px;
  }
  .card--front .brand-mark__square { width: 34px; height: 34px; }

  .divider {
    position: absolute; left: 424px; top: 100px; width: 3px; height: 255px;
    background: linear-gradient(to bottom, rgba(138,138,138,0), var(--divider) 30%, var(--divider) 70%, rgba(138,138,138,0));
  }

  .identity { position: absolute; left: 493px; top: 100px; }
  .identity__name { font-size: 42px; font-weight: 700; line-height: 1.1; color: var(--ink-dark); }
  .identity__role { font-size: 32px; font-weight: 400; line-height: 1.2; color: var(--ink-mid); }

  .contact-list { list-style: none; position: absolute; left: 496px; top: 230px; }
  .contact-list__item {
    display: flex; align-items: center; gap: 5px;
    font-size: 24px; line-height: 35px; color: var(--ink-mid);
  }
  .contact-list__icon { width: 15px; height: 15px; fill: var(--ink-mid); flex: none; }

  .address-band {
    position: absolute; left: 0; bottom: 0; width: 100%; height: 61px;
    background: var(--brand-red); color: var(--card-white);
    display: flex; align-items: center; justify-content: center;
    font-size: 23px;
  }

  .card--back .brand-mark {
    position: absolute; left: 0; right: 0; top: 200px; justify-content: center;
    font-size: 66px; gap: 22px;
  }
  .card--back .brand-mark__square { width: 60px; height: 60px; }
</style>
</head>
<body>
  <section class="card card--front">
    <div class="brand-mark">
      <span class="brand-mark__square"></span>
      <span class="brand-mark__name">Tall Oak Staffing</span>
    </div>

    <div class="divider"></div>

    <div class="identity">
      <p class="identity__name">Your Name</p>
      <p class="identity__role">Designation</p>
    </div>

    <ul class="contact-list">
      <li class="contact-list__item">
        <svg class="contact-list__icon" viewBox="0 0 16 16"><path d="M1 6c0-2 3-3 7-3s7 1 7 3v1h-4V6H5v1H1zM3 8h10l1 6H2z"/></svg>
        123-123-1234
      </li>
      <li class="contact-list__item">
        <svg class="contact-list__icon" viewBox="0 0 16 16"><path d="M1 4h14v9H1zM2 5v.5l6 4 6-4V5zm0 2v5h12V7l-6 4z" fill-rule="evenodd"/></svg>
        info@yourwebsite.com
      </li>
      <li class="contact-list__item">
        <svg class="contact-list__icon" viewBox="0 0 16 16"><circle cx="8" cy="8" r="7"/></svg>
        www.talloakstaffing.com
      </li>
    </ul>

    <div class="address-band">1234, Street Name, City, District, Country Code.</div>
  </section>

  <section class="card card--back">
    <div class="brand-mark">
      <span class="brand-mark__square"></span>
      <span class="brand-mark__name">Tall Oak Staffing</span>
    </div>
  </section>
</body>
</html>
```